Ridgeway Mining Solutions Business Card

Ridgeway Mining Solutions is a company that provides consulting services to the Mining Industry.

Whilst Ridgeway Mining Solutions is an Australian based company its client base is the global mining industry.

The essence of Ridgeway Mining Solutions is its a can do organisation that can make a difference to its clients by providing quality assistance and form lasting relationships.
Updates

Target Market(s)

The global Mining Industry.

Industry/Entity Type

Mining

Font styles to use
Serif

Colors

Designer to choose colors to be used in the design.

Requirements
Nice to have
• My thinking is the card would look good in black given the logo.

I would like to see written on the back side of the card " Providing Metallurgical, Management and Corporate Services to the Mining Industry"

```html
<!DOCTYPE html>
<html lang="en">
<head>
<meta charset="utf-8">
<title>Ridgeway Mining Solutions – Business Card</title>
<link rel="stylesheet" href="https://fonts.googleapis.com/css2?family=Poppins:wght@300;400;600&display=swap">
<style>
  :root {
    --stage: #cdcdcd;
    --card: #0b0b0b;
    --orange: #f29a1a;
    --white: #f4f4f4;
    --rock-dark: #3a2a18;
    --rock-mid: #7a5426;
    --rock-light: #c98a34;
  }
  * { margin: 0; padding: 0; box-sizing: border-box; }
  html, body {
    width: 1200px;
    height: 873px;
    overflow: hidden;
    background: var(--stage);
    font-family: "Poppins", sans-serif;
  }
  .stage {
    position: relative;
    width: 1200px;
    height: 873px;
    display: flex;
    align-items: center;
    justify-content: center;
    gap: 40px;
  }
  .card {
    position: relative;
    width: 520px;
    height: 297px;
    background: var(--card);
    overflow: hidden;
    box-shadow: 0 10px 24px rgba(0,0,0,0.25);
  }
  .card-art {
    position: absolute;
    inset: 0;
    width: 100%;
    height: 100%;
  }
  .wordmark {
    position: absolute;
    font-weight: 600;
    color: var(--orange);
    letter-spacing: 0.02em;
    line-height: 1.15;
  }
  .front .wordmark {
    left: 300px;
    top: 92px;
    width: 200px;
    font-size: 16px;
  }
  .holder-name {
    position: absolute;
    left: 252px;
    top: 158px;
    font-size: 32px;
    font-weight: 300;
    color: var(--orange);
  }
  .holder-role {
    position: absolute;
    left: 256px;
    top: 204px;
    font-size: 11px;
    font-weight: 300;
    color: var(--white);
  }
  .contact {
    position: absolute;
    left: 22px;
    bottom: 18px;
    font-size: 10.5px;
    font-weight: 300;
    color: var(--white);
    line-height: 1.7;
  }
  .photo {
    position: absolute;
    background: linear-gradient(135deg, var(--rock-dark) 0%, var(--rock-mid) 45%, var(--rock-light) 75%, var(--rock-dark) 100%);
  }
  .back .photo-top {
    left: 92px;
    top: 0;
    width: 150px;
    height: 72px;
  }
  .back .photo-bottom {
    left: 322px;
    top: 190px;
    width: 198px;
    height: 107px;
    background: linear-gradient(160deg, var(--rock-light) 0%, var(--rock-mid) 50%, var(--rock-dark) 100%);
  }
  .back .brand-block {
    position: absolute;
    left: 0;
    right: 0;
    top: 100px;
    text-align: center;
  }
  .back .wordmark {
    position: static;
    font-size: 20px;
  }
  .tagline {
    margin-top: 8px;
    font-size: 9.5px;
    font-weight: 300;
    color: var(--white);
    line-height: 1.5;
  }
</style>
</head>
<body>
<main class="stage">

  <section class="card front" aria-label="Business card front">
    <svg class="card-art" viewBox="0 0 520 297" aria-hidden="false">
      <defs>
        <linearGradient id="tunnelTone" x1="0" y1="0" x2="1" y2="1">
          <stop offset="0" stop-color="#3a2a18"/>
          <stop offset="0.5" stop-color="#9a6a2c"/>
          <stop offset="1" stop-color="#2a1e12"/>
        </linearGradient>
      </defs>
      <polygon class="accent-frame" fill="#f29a1a"
        points="0,0 282,0 264,36 308,80 258,88 206,162 166,142 0,168"/>
      <polygon class="photo-tunnel" role="img" aria-label="Photograph of a lit underground mine tunnel"
        fill="url(#tunnelTone)"
        points="0,0 264,0 248,34 286,74 250,80 202,150 162,130 0,152"/>
    </svg>
    <div class="wordmark">Ridgeway Mining Solutions</div>
    <div class="holder-name">Name Here</div>
    <div class="holder-role">Position Here ex. Engineer</div>
    <div class="contact">
      <p>27 Quarry Lane Kalgoorlie WA 6430 Australia</p>
      <p>Phone : +61 8 9021 4470 &nbsp; Email : info@ridgewaymining.com</p>
    </div>
  </section>

  <section class="card back" aria-label="Business card back">
    <div class="photo photo-top" role="img" aria-label="Photograph of mining machinery at a dig site"></div>
    <div class="brand-block">
      <div class="wordmark">Ridgeway Mining Solutions</div>
      <p class="tagline">Providing Metallurgical, Management and<br>Corporate Services to the Mining Industry</p>
    </div>
    <div class="photo photo-bottom" role="img" aria-label="Photograph of a haul truck tyre and ore at an open pit"></div>
  </section>

</main>
</body>
</html>
```